Brightmill Data Works

Our company is about IT hardwares and IT solutions. IT hardware such as PC, RAMS, storage and servers. IT solutions such as project management, BA. We are also selling new technology too.

Target Market(s)

Consumer, Small to Medium Business, Corporate

Requirements
Must have
• The business card must have the following:
• Name:
• Title:
• Contact Number:
• Email address:
• Website:
• Color: Must match the logo color upgrade

```html
<!DOCTYPE html>
<html lang="en">
<head>
<meta charset="utf-8">
<title>Brightmill Data Works – Business Card</title>
<link rel="stylesheet" href="https://fonts.googleapis.com/css2?family=Open+Sans:wght@400;600&family=Saira+Condensed:wght@700&display=swap">
<style>
  :root {
    --page-bg: #2b2b2d;
    --card-bg: #1d1e20;
    --card-bg-back: #18191b;
    --pattern-a: #2a2b2e;
    --pattern-b: #1c1d1f;
    --ink-white: #f4f4f4;
    --ink-orange: #e0902a;
    --rule-grey: #6a6a6a;
  }
  * { box-sizing: border-box; margin: 0; padding: 0; }
  html, body {
    width: 1200px; height: 1108px; overflow: hidden;
    background: var(--page-bg);
  }
  .stage {
    position: relative; width: 1200px; height: 1108px;
    display: flex; justify-content: center; align-items: center; gap: 60px;
  }
  .card {
    position: relative; width: 420px; height: 660px;
    border-radius: 26px; overflow: hidden;
    background: var(--card-bg);
    box-shadow: 0 18px 40px rgba(0,0,0,.45);
  }
  /* Front */
  .card-front {
    display: flex; flex-direction: column; align-items: center;
    padding-top: 110px; text-align: center;
  }
  .brand-dot {
    width: 54px; height: 54px; border-radius: 50%;
    background: var(--ink-orange);
    margin-bottom: 26px;
  }
  .brand-name {
    font-family: "Saira Condensed", sans-serif; font-weight: 700;
    font-size: 50px; line-height: 0.95; letter-spacing: 1px;
    color: var(--ink-white); text-transform: uppercase;
  }
  .person-name {
    margin-top: 64px;
    font-family: "Open Sans", sans-serif; font-weight: 400;
    font-size: 27px; letter-spacing: 0.5px;
    color: var(--ink-orange); text-transform: uppercase;
  }
  .person-title {
    margin-top: 2px;
    font-family: "Open Sans", sans-serif; font-weight: 400;
    font-size: 16px; letter-spacing: 0.5px;
    color: var(--ink-white); text-transform: uppercase;
  }
  .contact-divider {
    margin-top: 30px; width: 190px;
    display: flex; align-items: center; gap: 8px;
  }
  .contact-divider .rule { flex: 1; height: 1px; background: var(--rule-grey); }
  .contact-divider .icons { display: flex; gap: 4px; }
  .contact-list {
    margin-top: 12px; list-style: none;
    font-family: "Open Sans", sans-serif; font-weight: 400;
    font-size: 17px; line-height: 1.5; letter-spacing: 0.3px;
    color: var(--ink-white); text-transform: uppercase;
  }
  /* Back */
  .card-back { background: var(--card-bg-back); }
  .pattern-field {
    position: absolute; inset: 0;
    background: linear-gradient(160deg, var(--pattern-a) 0%, var(--pattern-b) 80%);
  }
  .back-brand {
    position: absolute; left: 0; right: 0; bottom: 90px;
    text-align: center;
    font-family: "Saira Condensed", sans-serif; font-weight: 700;
    font-size: 50px; line-height: 0.95; letter-spacing: 1px;
    color: var(--ink-white); text-transform: uppercase;
  }
</style>
</head>
<body>
<main class="stage">
  <section class="card card-front" aria-label="Business card front">
    <div class="brand-dot"></div>
    <h1 class="brand-name">Brightmill<br>Data Works</h1>
    <p class="person-name">Daniel Okafor</p>
    <p class="person-title">Managing Director</p>
    <div class="contact-divider">
      <span class="rule"></span>
      <span class="icons">
        <svg width="18" height="18" viewBox="0 0 18 18" aria-label="Phone"><circle cx="9" cy="9" r="9" fill="#e0902a"/><path d="M6 5.5c0 3.5 3 6.5 6.5 6.5l.6-1.6-1.8-.8-.8.9c-1.2-.5-2.2-1.5-2.7-2.7l.9-.8-.8-1.8z" fill="#1d1e20"/></svg>
        <svg width="18" height="18" viewBox="0 0 18 18" aria-label="Email"><circle cx="9" cy="9" r="9" fill="#e0902a"/><rect x="5" y="6" width="8" height="6" rx="1" fill="#1d1e20"/><path d="M5.5 6.5 9 9.3l3.5-2.8" stroke="#e0902a" stroke-width="0.9" fill="none"/></svg>
        <svg width="18" height="18" viewBox="0 0 18 18" aria-label="Website"><circle cx="9" cy="9" r="9" fill="#e0902a"/><circle cx="9" cy="9" r="4.2" fill="none" stroke="#1d1e20" stroke-width="1.2"/><path d="M4.8 9h8.4M9 4.8c-1.8 2.4-1.8 6 0 8.4M9 4.8c1.8 2.4 1.8 6 0 8.4" stroke="#1d1e20" stroke-width="1" fill="none"/></svg>
      </span>
      <span class="rule"></span>
    </div>
    <ul class="contact-list">
      <li>444 555 0192</li>
      <li>hello@brightmilldata.com</li>
      <li>www.brightmilldata.com</li>
    </ul>
  </section>

  <section class="card card-back" aria-label="Business card back">
    <div class="pattern-field" role="img" aria-label="Faint repeating brand pattern across the card back"></div>
    <p class="back-brand">Brightmill<br>Data Works</p>
  </section>
</main>
</body>
</html>
```